Preschool Website

Looking to have a one page splash with a contact us form that uses some kind of verification to keep bots from filling out the form. We would like for it to be dynamic for both mobile and desktop. Would like to have it show up in search engines for preschool in are area. Would like to include a link to the website are current parents use for payment information.

Target Market(s)

Young Adults with Childrens

Industry/Entity Type

Preschool

Coding

Coded - Design and coding required

Number of Pages Required

1 page

Colors

Designer to choose colors to be used in the design.

Requirements
Must have
• Searchable in Quorla
• Contact us form
• Name
• Phone
• Email
• Message box
• Form must have code entered to submit to prevent junk emails
• Link to the website we use for parents to make payments
• our phone and address clickable on device to make call or map on phone
Should not have
• more then one page

```html
<!DOCTYPE html>
<html lang="en">
<head>
<meta charset="utf-8">
<title>Maplewood Preschool – Landing Page Variants</title>
<link href="https://fonts.googleapis.com/css2?family=Montserrat:wght@400;500;600;700&family=Roboto:wght@400&display=swap" rel="stylesheet">
<style>
  :root{
    --page:#efefef;
    --white:#ffffff;
    --ink:#222222;
    --muted:#555555;
    --teal:#2bb5bf;
    --orange:#f7951d;
    --black:#1d1d1d;
    --sky:#d8e8f6;
    --violet-1:#5560a6;
    --violet-2:#7e4fa6;
    --violet-3:#a948a8;
  }
  *{box-sizing:border-box;margin:0;padding:0}
  html,body{width:836px;height:1200px;overflow:hidden;background:var(--page)}
  .stage{width:1500px;height:2154px;transform:scale(.55733);transform-origin:0 0;position:relative}
  .page{position:absolute;left:80px;width:1340px;height:962px;background:var(--white);overflow:hidden;box-shadow:0 1px 3px rgba(0,0,0,.18)}
  .page--one{top:97px}
  .page--two{top:1114px}

  .hero-band{position:absolute;left:0;top:0;width:1340px;height:298px}
  .page--one .hero-band{background:var(--sky)}
  .page--two .hero-band{background:var(--white)}

  .top-bar{position:absolute;left:0;top:0;width:1340px;height:170px}
  .contact{position:absolute;color:var(--white);font-family:"Montserrat",sans-serif;font-size:25px;text-decoration:none;display:flex;align-items:flex-start;gap:14px;line-height:37px}
  .contact svg{flex:none;fill:var(--white)}
  .contact--phone{left:98px;top:24px}
  .contact--phone svg{margin-top:5px}
  .contact--address{left:928px;top:9px}
  .contact--address svg{margin-top:7px;margin-right:10px}

  .brand{position:absolute;left:100px;top:168px;display:flex;align-items:center;gap:38px;text-decoration:none}
  .brand-mark{width:128px;height:118px;display:flex;align-items:center;justify-content:center}
  .brand-mark span{display:block;width:96px;height:96px;border-radius:50%;background:var(--teal)}
  .brand-name{font-family:"Montserrat",sans-serif;font-weight:600;font-size:35px;letter-spacing:.5px;color:var(--ink);text-transform:uppercase}

  .payment-link{position:absolute;left:1063px;top:173px;width:181px;height:58px;background:var(--teal);color:var(--white);font-family:"Montserrat",sans-serif;font-size:26px;display:flex;align-items:center;justify-content:center;text-decoration:none}

  .photo{position:absolute;left:0;top:298px;width:807px;height:504px}
  .page--one .photo{background:linear-gradient(100deg,#cfb39a 0%,#b88a6c 30%,#e0c066 55%,#8fb6c9 80%,#d9d3c6 100%)}
  .page--two .photo{background:linear-gradient(100deg,#c54a3b 0%,#d9c2ad 28%,#e8d9c8 50%,#c7a58a 72%,#9cb28a 100%)}
  .photo-edge{position:absolute;left:1238px;top:298px;width:102px;height:504px;background:linear-gradient(180deg,#eec372 0%,#c7a77a 50%,#e0bd7a 100%)}

  .tab{position:absolute;top:256px;width:0;height:0;border-bottom:42px solid var(--black)}
  .tab--left{left:750px;border-left:57px solid transparent}
  .tab--right{left:1238px;border-right:52px solid transparent}

  .enquiry{position:absolute;left:807px;top:256px;width:431px;height:546px;padding:0 34px}
  .page--one .enquiry{background:var(--orange)}
  .page--two .enquiry{background:var(--teal)}
  .enquiry h2{font-family:"Montserrat",sans-serif;font-weight:500;font-size:43px;color:var(--white);text-align:center;margin:40px 0 28px;line-height:52px}
  .field{display:flex;height:54px;margin-bottom:12px;background:var(--white)}
  .field--message{height:115px;margin-bottom:20px}
  .field-icon{width:58px;height:54px;flex:none;display:flex;align-items:center;justify-content:center}
  .page--one .field-icon{background:var(--black)}
  .page--two .field-icon{background:var(--orange)}
  .field-icon svg{width:20px;height:20px;fill:none;stroke:var(--white);stroke-width:2}
  .field-icon svg.solid{fill:var(--white);stroke:none}
  .field input,.field textarea{flex:1;border:0;outline:0;background:transparent;font-family:"Montserrat",sans-serif;font-size:17px;color:var(--muted);padding:0 24px;resize:none}
  .field textarea{padding-top:16px}
  .field input::placeholder,.field textarea::placeholder{color:var(--muted)}
  .submit{width:366px;height:63px;border:1px solid rgba(255,255,255,.7);color:var(--white);font-family:"Montserrat",sans-serif;font-size:24px;letter-spacing:.5px}
  .page--one .submit{background:var(--teal)}
  .page--two .submit{background:var(--orange)}

  .footer{position:absolute;left:0;top:802px;width:1340px;height:160px;text-align:center}
  .legal{font-family:"Roboto",sans-serif;font-size:18px;color:#333;margin-top:53px}
  .legal a{color:inherit;text-decoration:none}
  .social{display:flex;justify-content:center;gap:24px;margin-top:36px}
  .social a{display:block;width:20px;height:20px;border-radius:50%;background:var(--teal)}
</style>
</head>
<body>
<svg width="0" height="0" style="position:absolute" aria-hidden="true">
  <defs>
    <linearGradient id="sky-grad" x1="0" x2="1" y1="0" y2="0">
      <stop offset="0" stop-color="#5560a6"/>
      <stop offset=".5" stop-color="#7e4fa6"/>
      <stop offset="1" stop-color="#a948a8"/>
    </linearGradient>
    <symbol id="i-phone" viewBox="0 0 24 24"><path d="M6.6 2.5l3 3.6-2 2.4c1.2 2.9 3.6 5.3 6.5 6.6l2.4-2 3.6 3-1.6 3.3c-.5.9-1.6 1.3-2.6 1C8.6 18.3 5.3 15 3.2 7.6c-.3-1 .1-2.1 1-2.6z"/></symbol>
    <symbol id="i-pin" viewBox="0 0 24 30"><path d="M12 0C5.4 0 0 5.2 0 11.7 0 20 12 30 12 30s12-10 12-18.3C24 5.2 18.6 0 12 0zm0 16a4.5 4.5 0 110-9 4.5 4.5 0 010 9z"/></symbol>
    <symbol id="i-user" viewBox="0 0 24 24"><circle cx="12" cy="8" r="4.5"/><path d="M4 21v-1.5C4 16.5 7 15 12 15s8 1.5 8 4.5V21z"/></symbol>
    <symbol id="i-mail" viewBox="0 0 24 24"><rect x="3" y="5.5" width="18" height="13" rx="1"/><path d="M3.5 6.5l8.5 6.5 8.5-6.5"/></symbol>
    <symbol id="i-chat" viewBox="0 0 24 24"><path d="M12 4c4.7 0 8.5 2.8 8.5 6.3S16.7 16.6 12 16.6c-1 0-2 -.1-2.9-.4L4.5 19l1.3-4C4.3 13.8 3.5 12.1 3.5 10.3 3.5 6.8 7.3 4 12 4z"/></symbol>
  </defs>
</svg>

<main class="stage">

  <section class="page page--one" aria-label="Landing page, orange form variant">
    <div class="hero-band"></div>
    <svg class="top-bar" viewBox="0 0 1340 170" aria-hidden="true">
      <path fill="url(#sky-grad)" d="M0 0H1340V112A70 40 0 0 1 1160 100A75 60 0 0 1 1025 108A100 70 0 0 1 800 115A110 60 0 0 1 560 112A70 40 0 0 1 425 118A150 80 0 0 1 175 128A70 40 0 0 1 75 130A60 30 0 0 1 0 128Z"/>
    </svg>
    <a class="contact contact--phone" href="tel:5550142288"><svg width="26" height="26"><use href="#i-phone"/></svg>555-014-2288</a>
    <a class="contact contact--address" href="https://maps.example.com/?q=12B+Orchard+Rise+Dunmore"><svg width="22" height="28"><use href="#i-pin"/></svg><span>12B Orchard Rise,Dunmore<br>County Westford, Ireland</span></a>

    <a class="brand" href="#"><span class="brand-mark"><span></span></span><span class="brand-name">Maplewood Preschool</span></a>
    <a class="payment-link" href="#">Payment</a>

    <div class="photo" role="img" aria-label="Photo of smiling preschool children drawing at a classroom table"></div>
    <div class="photo-edge" role="img" aria-label="Soft-focus classroom background"></div>

    <span class="tab tab--left"></span><span class="tab tab--right"></span>
    <form class="enquiry">
      <h2>Get Started</h2>
      <label class="field"><span class="field-icon"><svg><use href="#i-user"/></svg></span><input type="text" placeholder="Name"></label>
      <label class="field"><span class="field-icon"><svg class="solid"><use href="#i-phone"/></svg></span><input type="tel" placeholder="Phone Number"></label>
      <label class="field"><span class="field-icon"><svg><use href="#i-mail"/></svg></span><input type="email" placeholder="Email"></label>
      <label class="field field--message"><span class="field-icon"><svg><use href="#i-chat"/></svg></span><textarea placeholder="Message"></textarea></label>
      <button class="submit" type="button">SUBMIT</button>
    </form>

    <footer class="footer">
      <p class="legal">© 2019 All Rights Reserved | <a href="#">Privacy Policy</a> | <a href="#">Terms and Conditions</a> | <a href="#">Impressum</a></p>
      <nav class="social"><a href="#" aria-label="Social link 1"></a><a href="#" aria-label="Social link 2"></a><a href="#" aria-label="Social link 3"></a><a href="#" aria-label="Social link 4"></a><a href="#" aria-label="Social link 5"></a></nav>
    </footer>
  </section>

  <section class="page page--two" aria-label="Landing page, teal form variant">
    <div class="hero-band"></div>
    <svg class="top-bar" viewBox="0 0 1340 170" aria-hidden="true">
      <path fill="url(#sky-grad)" d="M0 0H1340V112A70 40 0 0 1 1160 100A75 60 0 0 1 1025 108A100 70 0 0 1 800 115A110 60 0 0 1 560 112A70 40 0 0 1 425 118A150 80 0 0 1 175 128A70 40 0 0 1 75 130A60 30 0 0 1 0 128Z"/>
    </svg>
    <a class="contact contact--phone" href="tel:5550142288"><svg width="26" height="26"><use href="#i-phone"/></svg>555-014-2288</a>
    <a class="contact contact--address" href="https://maps.example.com/?q=12B+Orchard+Rise+Dunmore"><svg width="22" height="28"><use href="#i-pin"/></svg><span>12B Orchard Rise,Dunmore<br>County Westford, Ireland</span></a>

    <a class="brand" href="#"><span class="brand-mark"><span></span></span><span class="brand-name">Maplewood Preschool</span></a>
    <a class="payment-link" href="#">Payment</a>

    <div class="photo" role="img" aria-label="Photo of a cheerful boy giving a thumbs up with children playing in a colourful classroom"></div>
    <div class="photo-edge" role="img" aria-label="Soft-focus classroom background"></div>

    <span class="tab tab--left"></span><span class="tab tab--right"></span>
    <form class="enquiry">
      <h2>Get Started</h2>
      <label class="field"><span class="field-icon"><svg><use href="#i-user"/></svg></span><input type="text" placeholder="Name"></label>
      <label class="field"><span class="field-icon"><svg class="solid"><use href="#i-phone"/></svg></span><input type="tel" placeholder="Phone Number"></label>
      <label class="field"><span class="field-icon"><svg><use href="#i-mail"/></svg></span><input type="email" placeholder="Email"></label>
      <label class="field field--message"><span class="field-icon"><svg><use href="#i-chat"/></svg></span><textarea placeholder="Message"></textarea></label>
      <button class="submit" type="button">SUBMIT</button>
    </form>

    <footer class="footer">
      <p class="legal">© 2019 All Rights Reserved | <a href="#">Privacy Policy</a> | <a href="#">Terms and Conditions</a> | <a href="#">Impressum</a></p>
      <nav class="social"><a href="#" aria-label="Social link 1"></a><a href="#" aria-label="Social link 2"></a><a href="#" aria-label="Social link 3"></a><a href="#" aria-label="Social link 4"></a><a href="#" aria-label="Social link 5"></a></nav>
    </footer>
  </section>

</main>
</body>
</html>
```